Zeltrova - Clever Automation

We are a software house for Audio Visual Systems integration/automation and home automation. we develop innovative software to automate a variety of devices mainly related to audio visuals and we design touch panel user interfaces to control these systems.

We would like to see designs that stick to our colours and theme, which you can find on our webpage www.zeltrova.com.au

The final design should communicate touch panels, innovation, software and automation.

Industry/Entity Type

Software

Requirements
Must have
• The business card must show the following information:
Name example : Derek Thalwin
Qualification example: B Eng ICT(CompSys) Dip EngPrac
Title example : Control Systems Programmer
Mobile Phone, Company phone, Email address ,Company website

```html
<!DOCTYPE html>
<html lang="en">
<head>
<meta charset="utf-8">
<title>Zeltrova – Business Card</title>
<link rel="stylesheet" href="https://fonts.googleapis.com/css2?family=Questrial&family=Exo+2:wght@600&display=swap">
<style>
  :root {
    --backdrop: #2b2b2b;
    --card-white: #ffffff;
    --brand-blue: #2476bf;
    --brand-green: #1e9b55;
    --ink: #222222;
    --on-blue: #ffffff;
  }
  * { box-sizing: border-box; margin: 0; padding: 0; }
  html, body { width: 1200px; height: 750px; overflow: hidden; }
  body {
    position: relative;
    background: var(--backdrop);
    font-family: "Questrial", "Century Gothic", sans-serif;
  }
  .card {
    position: absolute;
    width: 511px;
    height: 291px;
    border-radius: 12px;
    overflow: hidden;
  }
  .card--front { left: 76px; top: 118px; background: var(--card-white); }
  .card--back { left: 612px; top: 325px; background: var(--brand-blue); }

  .front-head { position: absolute; inset: 0 0 auto 0; height: 162px; }
  .accent-line { position: absolute; left: 0; right: 0; top: 162px; height: 5px; background: var(--brand-green); }
  .front-foot { position: absolute; left: 0; right: 0; top: 167px; bottom: 0; background: var(--brand-blue); color: var(--on-blue); }

  .brand { position: absolute; display: flex; align-items: center; }
  .brand__square { display: block; border-radius: 6px; }
  .brand__name { font-family: "Questrial", sans-serif; letter-spacing: -0.5px; line-height: 1; }
  .brand--front { left: 19px; top: 15px; }
  .brand--front .brand__square { width: 62px; height: 56px; background: var(--brand-blue); }
  .brand--front .brand__name { margin-left: 10px; font-size: 32px; color: var(--brand-green); }
  .tagline--front {
    position: absolute; left: 93px; top: 56px;
    font-size: 7px; color: var(--brand-blue); letter-spacing: 0.2px;
  }

  .person { position: absolute; right: 62px; top: 76px; text-align: right; }
  .person__name { font-family: "Exo 2", sans-serif; font-weight: 600; font-size: 21px; color: var(--brand-blue); line-height: 1.1; }
  .person__title { font-size: 13px; color: var(--ink); margin-top: 5px; }

  .address { position: absolute; right: 311px; top: 57px; text-align: right; font-size: 12.5px; line-height: 16px; }
  .divider { position: absolute; left: 213px; top: 19px; width: 1px; height: 77px; background: var(--on-blue); opacity: 0.85; }
  .contacts { position: absolute; left: 226px; top: 25px; list-style: none; font-size: 12.5px; }
  .contacts li { display: flex; align-items: center; height: 16.7px; }
  .contacts svg { width: 11px; height: 11px; margin-right: 9px; flex: none; }

  .brand--back { left: 129px; top: 110px; }
  .brand--back .brand__square { width: 80px; height: 70px; background: var(--on-blue); border-radius: 8px; }
  .brand--back .brand__name { margin-left: 12px; font-size: 40px; color: var(--on-blue); }
  .tagline--back { position: absolute; left: 292px; top: 160px; font-size: 8px; color: var(--on-blue); }
  .back-web { position: absolute; left: 0; right: 0; bottom: 12px; text-align: center; font-size: 13px; color: var(--on-blue); letter-spacing: 0.3px; }
</style>
</head>
<body>

<section class="card card--front" aria-label="Business card front">
  <div class="front-head">
    <div class="brand brand--front">
      <span class="brand__square" aria-hidden="true"></span>
      <span class="brand__name">zeltrova</span>
    </div>
    <p class="tagline--front">Clever Automation</p>
    <div class="person">
      <p class="person__name">Derek Thalwin</p>
      <p class="person__title">Control Systems Programmer</p>
    </div>
  </div>
  <div class="accent-line"></div>
  <div class="front-foot">
    <p class="address">12 Millbrook Lane<br>Carrowdale, NSW, 2791</p>
    <div class="divider"></div>
    <ul class="contacts">
      <li>
        <svg viewBox="0 0 12 12" aria-hidden="true"><circle cx="6" cy="6" r="6" fill="#fff"/><rect x="4" y="2.5" width="4" height="7" rx="0.8" fill="#2476bf"/><rect x="4.7" y="3.3" width="2.6" height="4.3" fill="#fff"/></svg>
        0400 555 018
      </li>
      <li>
        <svg viewBox="0 0 12 12" aria-hidden="true"><circle cx="6" cy="6" r="6" fill="#fff"/><path d="M3.5 3.2c.3-.4.8-.4 1.1 0l.7.9c.2.3.1.6-.1.8l-.4.4c.4.9 1 1.5 1.9 1.9l.4-.4c.2-.2.6-.3.8-.1l.9.7c.4.3.4.8 0 1.1-.9.9-2.4.7-3.8-.7S2.6 4.1 3.5 3.2z" fill="#2476bf"/></svg>
        0255 500 147
      </li>
      <li>
        <svg viewBox="0 0 12 12" aria-hidden="true"><circle cx="6" cy="6" r="6" fill="#fff"/><rect x="2.8" y="3.8" width="6.4" height="4.4" rx="0.5" fill="#2476bf"/><path d="M3 4l3 2.3L9 4" stroke="#fff" stroke-width="0.7" fill="none"/></svg>
        dthalwin@zeltrova.com.au
      </li>
      <li>
        <svg viewBox="0 0 12 12" aria-hidden="true"><circle cx="6" cy="6" r="6" fill="#fff"/><circle cx="6" cy="6" r="3.5" fill="none" stroke="#2476bf" stroke-width="0.8"/><ellipse cx="6" cy="6" rx="1.5" ry="3.5" fill="none" stroke="#2476bf" stroke-width="0.7"/><path d="M2.5 6h7" stroke="#2476bf" stroke-width="0.7"/></svg>
        www.zeltrova.com.au
      </li>
    </ul>
  </div>
</section>

<section class="card card--back" aria-label="Business card back">
  <div class="brand brand--back">
    <span class="brand__square" aria-hidden="true"></span>
    <span class="brand__name">zeltrova</span>
  </div>
  <p class="tagline--back">Clever Automation</p>
  <p class="back-web">www.zeltrova.com.au</p>
</section>

</body>
</html>
```